Card Design for my dog training business Brightpaw Obedience

Need a business card design for my dog training business with my new logo. Want the card to come off professional yet fun. Want it to be very eye catchy as well. I normally have these at vet clinics, pet stores, and groomers. so need it to look better than my competitors.
Target Market(s)
dog owners
Industry/Entity Type
Dog Training
Contact Information for Business Card
needs logo, my name and info
Font styles to use
Serif
Colors
0255a3
ffffff
ec1f27
000000
333333
fbfbfb
Requirements
Must have
- Brightpaw Obedience
- Felix Orland
- 415 903 2276
- info@brightpawobedience.example
- www.brightpawobedience.example

```html
<!DOCTYPE html>
<html lang="en">
<head>
<meta charset="utf-8">
<title>Brightpaw Obedience – Business Card</title>
<link rel="stylesheet" href="https://fonts.googleapis.com/css2?family=Tinos:ital,wght@0,400;0,700;1,400&family=Roboto:wght@300&display=swap">
<style>
  :root {
    --page: #f2f2f2;
    --card-white: #ffffff;
    --card-black: #231f20;
    --back-dark: #111111;
    --back-mid: #242424;
    --silver: #a3a3a3;
    --tagline: #8c8c8c;
  }
  * { margin: 0; padding: 0; box-sizing: border-box; }
  html, body {
    width: 1125px; height: 1200px; overflow: hidden;
    background: var(--page);
  }
  .card {
    position: absolute; left: 150px;
    width: 825px; height: 471px;
    box-shadow: 0 2px 6px rgba(0,0,0,0.25);
  }
  .card svg { display: block; width: 100%; height: 100%; }
  .card-front { top: 98px; background: var(--card-white); }
  .card-back { top: 631px; }
  .brand-name { font-family: "Tinos", serif; font-weight: 400; }
  .person-name { font-family: "Tinos", serif; font-weight: 700; }
  .contact-line { font-family: "Roboto", sans-serif; font-weight: 300; }
  .tagline { font-family: "Tinos", serif; font-style: italic; }
</style>
</head>
<body>

<section class="card card-front" aria-label="Business card front">
  <svg viewBox="0 0 800 456" xmlns="http://www.w3.org/2000/svg">
    <rect class="front-base" width="800" height="456" fill="var(--card-white)"/>
    <path class="wave-band" fill="var(--card-black)"
      d="M0,275 C40,430 250,440 430,330 C580,240 710,195 800,240 L800,456 L0,456 Z"/>
    <path class="wave-swoosh" fill="var(--card-black)"
      d="M520,265 C620,185 740,170 800,225 L800,236 C740,195 630,205 520,265 Z"/>

    <g class="brand-lockup">
      <circle cx="110" cy="175" r="16" fill="var(--card-black)"/>
      <text class="brand-name" x="136" y="170" font-size="30" fill="var(--card-black)">Brightpaw</text>
      <text class="brand-name" x="136" y="202" font-size="30" fill="var(--card-black)">Obedience</text>
    </g>

    <text class="person-name" x="740" y="305" font-size="28" fill="var(--card-white)" text-anchor="end">Felix Orland</text>

    <g class="contact" fill="var(--card-white)">
      <text class="contact-line" x="712" y="349" font-size="17" text-anchor="end">415 903 2276</text>
      <text class="contact-line" x="712" y="375" font-size="17" text-anchor="end">info@brightpawobedience.example</text>
      <text class="contact-line" x="712" y="400" font-size="17" text-anchor="end">www.brightpawobedience.example</text>

      <path class="icon-phone" d="M724,336 c2,-1 3,0 4,2 l1,3 c0,1 -1,2 -2,2 c1,3 3,5 6,6 c0,-1 1,-2 2,-2 l3,1 c2,1 3,2 2,4 c-1,2 -3,3 -5,2 c-6,-2 -10,-6 -12,-12 c-1,-2 0,-5 1,-6 z"/>
      <g class="icon-mail">
        <rect x="723" y="366" width="16" height="11" rx="1"/>
        <path d="M723,367 L731,373 L739,367" fill="none" stroke="var(--card-black)" stroke-width="1.3"/>
      </g>
      <g class="icon-web">
        <circle cx="731" cy="395" r="8"/>
        <path d="M727,390 c2,1 4,2 3,4 c-1,2 -3,1 -3,3 M733,392 c2,0 3,2 2,4 M731,401 c1,-2 3,-2 4,-1" fill="none" stroke="var(--card-black)" stroke-width="1.5"/>
      </g>
    </g>
  </svg>
</section>

<section class="card card-back" aria-label="Business card back">
  <svg viewBox="0 0 800 456" xmlns="http://www.w3.org/2000/svg">
    <defs>
      <linearGradient id="back-sheen" x1="0" y1="0" x2="1" y2="1">
        <stop offset="0" stop-color="var(--back-dark)"/>
        <stop offset="0.45" stop-color="var(--back-mid)"/>
        <stop offset="1" stop-color="var(--back-dark)"/>
      </linearGradient>
    </defs>
    <rect class="back-base" width="800" height="456" fill="url(#back-sheen)"/>

    <g class="brand-lockup-large">
      <circle cx="400" cy="170" r="26" fill="var(--silver)"/>
      <text class="brand-name" x="400" y="262" font-size="54" fill="var(--silver)" text-anchor="middle">Brightpaw Obedience</text>
    </g>

    <text class="tagline" x="400" y="410" font-size="23" fill="var(--tagline)" text-anchor="middle">“Teaching good manners one patient walk at a time.”</text>
  </svg>
</section>

</body>
</html>
```